Kestrova - presentation for a remote DBA team offering data platform management

We need a website design for wordpress site called Kestrova.cz
We deliver remote database and data platform administration and development, oversee the database administrators, consult and train the personnel responsible for the database operations. The website should include several sections, home page with graphics elements supporting the name and service - remote dba work; blog section; service introduction and description, team introduction and description, download section for documents, presentations etc.

Target Market(s)

small and medium business companies requiring remote DBA service

Number of Pages Required

3 page

Font styles to use
Sans Serif

Colors

Designer to choose colors to be used in the design.

Requirements
Must have
• The website should have several sections to introduce the services, blog, team introduction, downloads

```html
<!DOCTYPE html>
<html lang="en">
<head>
<meta charset="utf-8">
<title>Kestrova.cz</title>
<link href="https://fonts.googleapis.com/css2?family=Roboto:wght@400;500;700&family=Lato:wght@400;700&display=swap" rel="stylesheet">
<style>
:root{
  --blue:#3e6fe2;
  --blue-dark:#2f57c4;
  --ink:#1e1e1e;
  --text:#666a70;
  --muted:#9a9ea5;
  --gray:#f3f3f3;
  --white:#ffffff;
  --line:#dcdcdc;
  --hero-dark:#1a1d22;
}
*{box-sizing:border-box;margin:0;padding:0}
html,body{width:1200px;height:4276px;overflow:hidden}
body{font-family:'Lato',sans-serif;color:var(--text);background:var(--white);position:relative}
.abs{position:absolute}
section,header,footer{position:absolute;left:0;width:1200px}
h2{font-family:'Roboto',sans-serif;font-weight:500;font-size:36px;color:var(--ink);text-align:center;position:absolute;left:0;width:1200px}
h2 span{color:var(--blue)}
.pill{position:absolute;background:var(--blue);color:var(--white);border-radius:30px;font-family:'Roboto',sans-serif;font-weight:700;font-size:17px;display:flex;align-items:center;justify-content:center;gap:12px;box-shadow:0 6px 14px rgba(62,111,226,.3)}
.center-text{position:absolute;text-align:center;font-size:15px;line-height:26px}
.photo{position:absolute}

/* Hero */
.hero{top:0;height:570px}
.hero-bg{position:absolute;inset:0;background:linear-gradient(135deg,#2a2e35 0%,#15171b 55%,#22262c 100%)}
.logo{left:77px;top:30px;font-family:'Roboto',sans-serif;font-size:30px;color:var(--white);position:absolute}
.nav{position:absolute;top:40px;left:0;width:1200px;font-family:'Roboto',sans-serif;font-size:13px;color:var(--white)}
.nav a{position:absolute;color:var(--white);text-decoration:none}
.nav .active{text-decoration:underline}
.search{position:absolute;left:1090px;top:30px;width:30px;height:30px;border-radius:50%;background:var(--blue)}
.hero-title{left:77px;top:228px;font-family:'Roboto',sans-serif;font-weight:700;font-size:32px;color:var(--blue);position:absolute}
.hero-text{left:77px;top:296px;width:470px;font-size:15px;line-height:24px;color:var(--white);position:absolute}

/* Services */
.service{position:absolute}
.service-icon{position:absolute;width:70px;height:78px}
.service h3{position:absolute;font-family:'Roboto',sans-serif;font-weight:700;font-size:16px;color:var(--ink);white-space:nowrap}
.service p{position:absolute;font-size:14px;line-height:25px;width:320px}
.service p a,.more{color:var(--blue);text-decoration:underline}

/* Team */
.member{position:absolute;top:1781px;width:236px;height:302px;border:1px solid var(--line);background:var(--white)}
.member-photo{position:absolute;left:0;top:0;width:234px;height:208px}
.member .socials{position:absolute;top:168px;left:0;width:234px;display:flex;justify-content:center;gap:18px}
.member .socials i{width:14px;height:14px;border-radius:50%;border:2px solid rgba(255,255,255,.85);display:block}
.member-name{position:absolute;top:230px;width:234px;text-align:center;font-family:'Roboto',sans-serif;font-weight:500;font-size:15px;color:var(--blue)}
.member-role{position:absolute;top:261px;width:234px;text-align:center;font-size:14px;color:var(--muted)}

/* Blog */
.post{position:absolute;top:2616px;width:271px;height:271px;overflow:hidden}
.post-img{position:absolute;inset:0}
.post .plus{position:absolute;left:117px;top:73px;width:38px;height:38px;border-radius:50%;background:var(--white);display:flex;align-items:center;justify-content:center;color:var(--blue);font-size:26px;font-family:'Roboto',sans-serif}
.post-card{position:absolute;left:0;bottom:0;width:271px;height:106px;background:rgba(240,240,240,.95);padding:14px 22px}
.post.featured .post-card{background:rgba(62,111,226,.9)}
.post time{font-size:12px;color:var(--muted);display:block}
.post h4{font-family:'Roboto',sans-serif;font-weight:700;font-size:16px;line-height:25px;color:var(--ink);margin-top:8px}
.post.featured time,.post.featured h4{color:var(--white)}

/* Contact */
.field{position:absolute;background:var(--white);border-radius:26px;font-size:14px;color:var(--muted);padding:0 22px;display:flex;align-items:center}
.field.area{align-items:flex-start;padding-top:20px;border-radius:30px}

/* Info */
.info{position:absolute;top:3777px;width:342px;text-align:center}
.info .ic{position:absolute;left:149px;top:62px;width:44px;height:44px;border-radius:50%;border:2px solid var(--blue-dark)}
.info h5{position:absolute;top:125px;width:342px;font-family:'Roboto',sans-serif;font-weight:700;font-size:17px;color:var(--blue-dark)}
.info p{position:absolute;top:157px;width:342px;font-size:14px;line-height:22px;color:var(--text)}
.divider{position:absolute;top:3830px;width:1px;height:170px;background:var(--line)}

/* Footer */
.footer-links{position:absolute;top:4094px;left:0;width:1200px;text-align:center;font-family:'Roboto',sans-serif;font-size:14px;color:var(--white);word-spacing:2px}
.footer-links span{margin:0 18px}
.footer-social{position:absolute;top:4150px;left:0;width:1200px;display:flex;justify-content:center;gap:14px}
.footer-social i{width:36px;height:36px;border-radius:50%;border:2px solid var(--white);display:block}
.footer-rule{position:absolute;top:4207px;left:77px;width:1046px;height:1px;background:rgba(255,255,255,.4)}
.copyright{position:absolute;left:77px;top:4232px;font-family:'Roboto',sans-serif;font-size:14px;color:var(--white)}
.footer-brand{position:absolute;right:77px;top:4220px;font-family:'Roboto',sans-serif;font-size:30px;color:var(--white)}
</style>
</head>
<body>

<header class="hero">
  <div class="hero-bg" role="img" aria-label="Dark photo of a team working at desks in an office"></div>
  <svg class="abs" style="left:0;top:470px" width="1200" height="100" viewBox="0 0 1200 100" aria-hidden="true">
    <path d="M0 20 Q600 140 1200 20 L1200 100 L0 100 Z" fill="var(--white)"/>
  </svg>
  <div class="logo">Kestrova.cz</div>
  <nav class="nav">
    <a class="active" style="left:541px">HOME</a>
    <a style="left:638px">ABOUT US</a>
    <a style="left:752px">SERVICES</a>
    <a style="left:866px">BLOG</a>
    <a style="left:957px">CONTACT US</a>
  </nav>
  <svg class="search" viewBox="0 0 30 30" aria-hidden="true">
    <circle cx="15" cy="15" r="15" fill="var(--blue)"/>
    <circle cx="13.5" cy="13.5" r="5" fill="none" stroke="#fff" stroke-width="2"/>
    <line x1="17" y1="17" x2="21" y2="21" stroke="#fff" stroke-width="2"/>
  </svg>
  <div class="hero-title">KESTROVA</div>
  <p class="hero-text">Lorem Ipsum is simply dummy text of the printing and typesetting industry. Lorem Ipsum has been ever since the 1500s.</p>
  <div class="pill" style="left:77px;top:393px;width:145px;height:44px">Get A Quote</div>
  <svg class="abs" style="left:650px;top:100px" width="480" height="460" viewBox="0 0 480 460">
    <defs>
      <linearGradient id="heroPhoto" x1="0" y1="0" x2="1" y2="1">
        <stop offset="0" stop-color="#d9d6d0"/><stop offset=".5" stop-color="#a9a39a"/><stop offset="1" stop-color="#6d6a66"/>
      </linearGradient>
    </defs>
    <path d="M140 10 Q200 -10 240 40 L330 150 Q360 30 440 110 Q500 190 430 300 Q380 380 300 400 L120 460 Q40 470 60 380 L40 250 Q20 120 140 10 Z" fill="var(--blue)"/>
    <path role="img" aria-label="Photo of colleagues gathered around a laptop" d="M110 40 Q200 -10 320 20 Q440 40 455 150 Q470 260 400 330 Q320 420 220 400 Q110 380 70 280 Q30 160 110 40 Z" fill="url(#heroPhoto)"/>
  </svg>
</header>

<section style="top:556px;height:500px">
  <h2 style="top:126px">Welcome To <span>Kestrova.cz</span></h2>
  <p class="center-text" style="left:280px;top:192px;width:640px">Lorem Ipsum is simply dummy text of the printing and typesetting industry. Lorem Ipsum has been the industry's standard dummy text ever since the 1500s, when an unknown printer took a galley of type and scrambled it to make a type specimen book.</p>
  <p class="center-text" style="left:280px;top:292px;width:640px">It has survived not only five centuries, but also the leap into electronic typesetting, remaining essentially unchanged.</p>
  <div class="pill" style="left:527px;top:384px;width:145px;height:50px">Read More</div>
</section>

<section style="top:1055px;height:605px;background:var(--gray)">
  <h2 style="top:56px">Our <span>Services</span></h2>
  <p class="center-text" style="left:290px;top:116px;width:620px">Lorem Ipsum is simply dummy text of the printing and typesetting industry. Lorem Ipsum has been the industry's standard dummy text ever since the 1500s.</p>
</section>

<div class="service" style="left:77px;top:1254px">
  <svg class="service-icon" viewBox="0 0 70 78" aria-hidden="true"><path d="M10 8 Q35 -4 60 14 Q72 40 58 66 Q34 82 12 66 Q-4 40 10 8Z" fill="var(--blue)"/><circle cx="36" cy="40" r="22" fill="var(--white)"/><rect x="26" y="32" width="20" height="16" rx="2" fill="var(--blue)"/></svg>
  <h3 style="left:105px;top:14px">Remote database</h3>
  <p style="left:105px;top:40px">Lorem Ipsum is simply dummy text of the printing and typesetting industry...<a>Read More</a></p>
</div>
<div class="service" style="left:180px;top:1382px">
  <svg class="service-icon" viewBox="0 0 70 78" aria-hidden="true"><path d="M10 8 Q35 -4 60 14 Q72 40 58 66 Q34 82 12 66 Q-4 40 10 8Z" fill="var(--blue)"/><circle cx="36" cy="40" r="22" fill="var(--white)"/><path d="M27 46 L27 36 L36 31 L45 36 L45 46 L36 51 Z" fill="var(--blue)"/></svg>
  <h3 style="left:108px;top:14px">Data platform administration</h3>
  <p style="left:108px;top:40px">Lorem Ipsum is simply dummy text of the printing and typesetting industry....<a>Read More</a></p>
</div>
<div class="service" style="left:77px;top:1510px">
  <svg class="service-icon" viewBox="0 0 70 78" aria-hidden="true"><path d="M10 8 Q35 -4 60 14 Q72 40 58 66 Q34 82 12 66 Q-4 40 10 8Z" fill="var(--blue)"/><circle cx="36" cy="40" r="22" fill="var(--white)"/><path d="M28 50 L44 30" stroke="var(--blue)" stroke-width="5" stroke-linecap="round"/></svg>
  <h3 style="left:105px;top:12px">Development</h3>
  <p style="left:105px;top:38px">Lorem Ipsum is simply dummy text of the printing and typesetting industry....<a>Read More</a></p>
</div>
<div class="photo" role="img" aria-label="Photo of a business meeting around a conference table" style="left:675px;top:1262px;width:437px;height:325px;background:linear-gradient(160deg,#e8ecef 0%,#b9c2c8 50%,#4a4f55 100%);box-shadow:0 6px 20px rgba(0,0,0,.18)"></div>
<svg class="abs" style="left:642px;top:1392px" width="56" height="56" viewBox="0 0 56 56" aria-hidden="true"><circle cx="28" cy="28" r="28" fill="var(--blue)" opacity=".85"/><path d="M23 19 L36 28 L23 37 Z" fill="#fff"/></svg>

<section style="top:1660px;height:485px">
  <h2 style="top:56px">Our <span>Team</span></h2>
</section>
<div class="member" style="left:77px">
  <div class="member-photo" role="img" aria-label="Portrait of a team member" style="background:linear-gradient(180deg,#d2d2d2,#3c3c3c)"></div>
  <svg class="abs" style="left:0;top:170px" width="234" height="40" viewBox="0 0 234 40" aria-hidden="true"><path d="M0 40 L0 30 Q117 -10 234 30 L234 40Z" fill="#fff"/></svg>
  <div class="socials"><i></i><i></i><i></i></div>
  <div class="member-name">Member Name</div><div class="member-role">Position</div>
</div>
<div class="member" style="left:345px">
  <div class="member-photo" role="img" aria-label="Portrait of a team member" style="background:linear-gradient(180deg,#d6d6d6,#404040)"></div>
  <svg class="abs" style="left:0;top:170px" width="234" height="40" viewBox="0 0 234 40" aria-hidden="true"><path d="M0 40 L0 30 Q117 -10 234 30 L234 40Z" fill="#fff"/></svg>
  <div class="socials"><i></i><i></i><i></i></div>
  <div class="member-name">Member Name</div><div class="member-role">Position</div>
</div>
<div class="member" style="left:616px">
  <div class="member-photo" role="img" aria-label="Portrait of a team member" style="background:linear-gradient(180deg,#d0d0d0,#383838)"></div>
  <svg class="abs" style="left:0;top:170px" width="234" height="40" viewBox="0 0 234 40" aria-hidden="true"><path d="M0 40 L0 30 Q117 -10 234 30 L234 40Z" fill="#fff"/></svg>
  <div class="socials"><i></i><i></i><i></i></div>
  <div class="member-name">Member Name</div><div class="member-role">Position</div>
</div>
<div class="member" style="left:886px">
  <div class="member-photo" role="img" aria-label="Portrait of a team member" style="background:linear-gradient(180deg,#d4d4d4,#3a3a3a)"></div>
  <svg class="abs" style="left:0;top:170px" width="234" height="40" viewBox="0 0 234 40" aria-hidden="true"><path d="M0 40 L0 30 Q117 -10 234 30 L234 40Z" fill="#fff"/></svg>
  <div class="socials"><i></i><i></i><i></i></div>
  <div class="member-name">Member Name</div><div class="member-role">Position</div>
</div>

<section style="top:2145px;height:345px;background:var(--gray)"></section>
<div class="photo" role="img" aria-label="Illustration spot: woman sitting cross-legged with a laptop, pointing" style="left:165px;top:2123px;width:260px;height:365px;background:linear-gradient(180deg,#e9d6c9 0%,#f4f1ee 40%,#7d93b6 100%);border-radius:120px 120px 20px 20px"></div>
<div class="abs" style="left:516px;top:2205px;font-family:'Roboto',sans-serif;font-weight:500;font-size:36px;color:var(--ink)">Download <span style="color:var(--blue)">Presentation</span></div>
<p class="abs" style="left:516px;top:2270px;width:600px;font-size:15px;line-height:26px">Lorem Ipsum is simply dummy text of the printing and typesetting industry. Lorem Ipsum has been the industry's standard printer took a galley of type and scrambled it to make a type specimen book.</p>
<div class="pill" style="left:516px;top:2377px;width:216px;height:52px">Download Now
  <svg width="22" height="22" viewBox="0 0 22 22" aria-hidden="true"><path d="M11 3 V14 M6 10 L11 15 L16 10 M3 15 V19 H19 V15" fill="none" stroke="#fff" stroke-width="2"/></svg>
</div>

<section style="top:2490px;height:460px">
  <h2 style="top:56px">Recent <span>Blog</span></h2>
</section>
<article class="post" style="left:151px">
  <div class="post-img" role="img" aria-label="Image of a digital network interface" style="background:linear-gradient(160deg,#1d4a5c,#0c2030)"></div>
  <div class="plus">+</div>
  <div class="post-card"><time>27, JULY 2018</time><h4>Lorem Ipsum is simply dummy text of the printing</h4></div>
</article>
<article class="post featured" style="left:465px">
  <div class="post-img" role="img" aria-label="Image of hands at work with documents" style="background:linear-gradient(160deg,#7d9ce8,#3e6fe2)"></div>
  <div class="plus">+</div>
  <div class="post-card"><time>27, JULY 2018</time><h4>Lorem Ipsum is simply dummy text of the printing</h4></div>
</article>
<article class="post" style="left:775px">
  <div class="post-img" role="img" aria-label="Image of connected technology icons" style="background:linear-gradient(160deg,#2a7f86,#0f3c46)"></div>
  <div class="plus">+</div>
  <div class="post-card"><time>27, JULY 2018</time><h4>Lorem Ipsum is simply dummy text of the printing</h4></div>
</article>

<section style="top:2950px;height:470px;background:var(--gray)">
  <h2 style="top:60px">Contact <span>Us</span></h2>
</section>
<div class="field" style="left:274px;top:3087px;width:319px;height:51px">Name*</div>
<div class="field" style="left:604px;top:3087px;width:322px;height:51px">E-mail*</div>
<div class="field" style="left:274px;top:3149px;width:319px;height:51px">Phone*</div>
<div class="field" style="left:604px;top:3149px;width:322px;height:51px">Subject</div>
<div class="field area" style="left:274px;top:3212px;width:652px;height:80px">Message</div>
<div class="pill" style="left:527px;top:3306px;width:145px;height:50px">Send Now</div>

<section style="top:3420px;height:357px">
  <h2 style="top:56px">Client <span>Testimonial</span></h2>
</section>
<svg class="abs" style="left:205px;top:3545px" width="122" height="126" viewBox="0 0 122 126" aria-hidden="true">
  <path d="M20 10 Q70 -8 110 30 Q128 80 96 112 Q50 134 16 104 Q-8 60 20 10Z" fill="var(--blue)"/>
</svg>
<div class="photo" role="img" aria-label="Portrait of the client" style="left:222px;top:3560px;width:86px;height:90px;border-radius:40px 46px 40px 44px;background:linear-gradient(180deg,#d8d3cc,#3b4048)"></div>
<p class="abs" style="left:362px;top:3553px;width:664px;font-size:15px;line-height:25px">Lorem Ipsum is simply dummy text of the printing and typesetting industry. Lorem Ipsum has been the industry's standard dummy text ever since the 1500s, when an unknown printer took a galley of type and scrambled it to make a type specimen book.</p>
<div class="abs" style="left:362px;top:3650px;font-family:'Roboto',sans-serif;font-weight:500;font-size:15px;color:var(--blue)">- Client Name</div>
<div class="abs" style="left:910px;top:3580px;font-family:'Roboto',sans-serif;font-weight:700;font-size:160px;line-height:1;color:#e4e8f0">”</div>
<svg class="abs" style="left:550px;top:3698px" width="100" height="14" viewBox="0 0 100 14" aria-hidden="true">
  <circle cx="7" cy="7" r="6" fill="none" stroke="#ccc"/>
  <circle cx="28" cy="7" r="6" fill="var(--blue)"/>
  <circle cx="49" cy="7" r="6" fill="none" stroke="#ccc"/>
  <circle cx="70" cy="7" r="6" fill="none" stroke="#ccc"/>
  <circle cx="91" cy="7" r="6" fill="none" stroke="#ccc"/>
</svg>

<section style="top:3777px;height:266px;background:var(--gray)"></section>
<div class="divider" style="left:419px"></div>
<div class="divider" style="left:781px"></div>
<div class="info" style="left:77px">
  <svg class="ic" viewBox="0 0 44 44" aria-hidden="true"><path d="M16 12 L20 16 L18 20 Q21 25 25 27 L29 25 L33 29 L30 33 Q20 33 12 22 Q11 15 16 12Z" fill="var(--blue-dark)"/></svg>
  <h5>Call Us</h5><p>123 456 7890</p>
</div>
<div class="info" style="left:429px">
  <svg class="ic" viewBox="0 0 44 44" aria-hidden="true"><path d="M22 33 Q13 23 13 18 A9 9 0 0 1 31 18 Q31 23 22 33Z" fill="none" stroke="var(--blue-dark)" stroke-width="2.5"/><circle cx="22" cy="18" r="3" fill="var(--blue-dark)"/></svg>
  <h5>Address</h5><p>123, Lorem ipsum is simply<br>dummy text of typesetting</p>
</div>
<div class="info" style="left:781px">
  <svg class="ic" viewBox="0 0 44 44" aria-hidden="true"><rect x="12" y="15" width="20" height="14" rx="1" fill="var(--blue-dark)"/><path d="M12 16 L22 23 L32 16" fill="none" stroke="#fff" stroke-width="1.5"/></svg>
  <h5>E-mail</h5><p>info@kestrova.cz</p>
</div>

<footer style="top:4043px;height:233px;background:var(--blue)"></footer>
<div class="footer-links">Home<span>|</span>About Us<span>|</span>Services<span>|</span>Blog<span>|</span>Contact Us</div>
<div class="footer-social" aria-hidden="true"><i></i><i></i><i></i><i></i></div>
<div class="footer-rule"></div>
<div class="copyright">© KESTROVA.CZ - 2018. All Rights Reserved.</div>
<div class="footer-brand">Kestrova.cz</div>

</body>
</html>
```